i need a business card for a plumbing company in california

we are a drain cleaning , maintenance plumbing company who is starting new marketing campaign for a tatrench-less pipe installation department .

Target Market(s)

the professional who appreciates time and quality workmanship.

Industry/Entity Type

Plumbing

Colors
0655a3
ec1f27

Requirements
Must have
• the second logo needs to be included
Nice to have
• a focus on the services offered
Should not have
• any underlined words on the brief

```html
<!DOCTYPE html>
<html lang="en">
<head>
<meta charset="utf-8">
<title>Clearline Plumbing — Business Card</title>
<link rel="stylesheet" href="https://fonts.googleapis.com/css2?family=Arimo:wght@400;700&family=Tinos:wght@400&display=swap">
<style>
  :root {
    --brand-blue: #0655a3;
    --brand-red: #ec1f27;
    --logo-grey: #76766e;
    --card-white: #f7f7f7;
    --stage: #2b2b2b;
    --text-dark: #333333;
    --white: #ffffff;
  }
  * { box-sizing: border-box; margin: 0; padding: 0; }
  html, body { width: 1200px; height: 997px; overflow: hidden; }
  body {
    background: var(--stage);
    font-family: "Arimo", Arial, sans-serif;
    position: relative;
  }
  .card {
    position: absolute;
    width: 540px;
    height: 309px;
    border-radius: 18px;
    background: var(--card-white);
    overflow: hidden;
  }
  .card svg.card-art { position: absolute; inset: 0; }
  .card-back { left: 60px; top: 150px; }
  .card-front { left: 600px; top: 440px; }

  .wordmark {
    position: absolute;
    font-weight: 700;
    color: var(--logo-grey);
    line-height: 1;
    display: flex;
    align-items: center;
    gap: 8px;
  }
  .wordmark .mark-dot {
    width: 14px; height: 14px; border-radius: 50%;
    background: var(--brand-red);
  }

  /* back */
  .card-back .wordmark { right: 34px; top: 40px; font-size: 28px; }
  .step-label {
    position: absolute;
    font-size: 12px;
    font-weight: 700;
    letter-spacing: 0.5px;
    text-transform: uppercase;
  }
  .step-label.red { color: var(--brand-red); }
  .step-label.blue { color: var(--brand-blue); }
  .tagline-pill {
    position: absolute;
    left: -14px; bottom: 22px;
    background: var(--brand-blue);
    color: var(--white);
    font-size: 13px;
    font-weight: 700;
    letter-spacing: 0.6px;
    padding: 8px 18px 8px 30px;
    border-radius: 0 20px 20px 0;
  }
  .tagline-pill em { font-style: normal; color: var(--brand-red); }

  /* front */
  .holder {
    position: absolute; left: 150px; top: 26px;
    font-size: 15px; font-weight: 700; color: var(--brand-red);
    text-transform: uppercase;
  }
  .holder .role { color: var(--text-dark); font-weight: 400; text-transform: none; margin-left: 8px; font-size: 14px; }
  .card-front .wordmark { left: 150px; top: 58px; font-size: 30px; }
  .services {
    position: absolute; left: 0; right: 0; top: 112px; height: 32px;
    background: var(--brand-blue);
    display: flex; align-items: center; justify-content: center; gap: 26px;
    color: var(--white); font-size: 14px; font-weight: 700;
  }
  .social {
    position: absolute; right: 26px; top: 158px;
    display: flex; flex-direction: column; align-items: flex-end; gap: 6px;
    font-size: 14px; font-weight: 700; color: var(--text-dark);
  }
  .social-row { display: flex; align-items: center; gap: 8px; }
  .social-row .dot { width: 10px; height: 10px; border-radius: 50%; background: var(--text-dark); }
  .badge-row { display: flex; gap: 8px; align-items: center; }
  .badge-row .dot { width: 12px; height: 12px; border-radius: 50%; background: var(--text-dark); }
  .badge-row .listing-badge { width: 64px; height: 18px; border-radius: 3px; background: var(--brand-blue); opacity: 0.85; }
  .contact {
    position: absolute; left: 26px; bottom: 16px;
    font-family: "Tinos", "Times New Roman", serif;
    color: var(--white); font-size: 16px;
    display: flex; flex-direction: column; gap: 4px;
  }
  .contact li { list-style: none; display: flex; align-items: center; gap: 10px; }
  .contact svg { width: 12px; height: 12px; flex: none; }
</style>
</head>
<body>

<section class="card card-back" aria-label="Card back">
  <svg class="card-art" viewBox="0 0 540 309" aria-hidden="true">
    <path d="M-10 268 C 120 196, 210 188, 300 160 S 460 104, 550 86" fill="none" stroke="var(--brand-red)" stroke-width="12"/>
    <path d="M-10 284 C 120 212, 210 204, 300 176 S 460 120, 550 102" fill="none" stroke="var(--brand-blue)" stroke-width="12"/>
    <g font-family="Arimo, Arial, sans-serif" font-weight="700" font-size="26" fill="#fff" text-anchor="middle">
      <circle cx="90" cy="226" r="21" fill="var(--brand-blue)" stroke="#fff" stroke-width="3"/>
      <text x="90" y="235">1</text>
      <circle cx="270" cy="172" r="21" fill="var(--brand-blue)" stroke="#fff" stroke-width="3"/>
      <text x="270" y="181">2</text>
      <circle cx="430" cy="122" r="21" fill="var(--brand-blue)" stroke="#fff" stroke-width="3"/>
      <text x="430" y="131">3</text>
    </g>
  </svg>
  <div class="wordmark"><span>Clearline Plumbing</span><span class="mark-dot"></span></div>
  <span class="step-label red" style="left:56px;top:256px;">Contact us.</span>
  <span class="step-label blue" style="left:232px;top:204px;">Buy online</span>
  <span class="step-label red" style="left:382px;top:154px;">Social media us</span>
  <div class="tagline-pill">LEAD BY <em>EXAMPLE</em></div>
</section>

<section class="card card-front" aria-label="Card front">
  <svg class="card-art" viewBox="0 0 540 309" aria-hidden="true">
    <path d="M0 228 C 140 196, 300 196, 540 220 L540 309 L0 309 Z" fill="var(--brand-red)"/>
    <path d="M0 262 C 160 222, 320 222, 540 236 L540 309 L0 309 Z" fill="var(--brand-blue)"/>
  </svg>
  <p class="holder">Marco Delgado<span class="role">Owner</span></p>
  <div class="wordmark"><span>Clearline Plumbing</span><span class="mark-dot"></span></div>
  <div class="services">
    <span>Sewer Drain Cleaning</span>
    <span>Maintenance</span>
    <span>Trenchless Re-Pipes</span>
  </div>
  <div class="social">
    <div class="social-row"><span class="dot"></span>/ClearlinePlumbing</div>
    <div class="social-row"><span class="dot"></span>@ClearlinePlumbing</div>
    <div class="badge-row"><span class="dot"></span><span class="dot"></span><span class="dot"></span><span class="listing-badge"></span></div>
  </div>
  <ul class="contact">
    <li><svg viewBox="0 0 12 12"><rect x="3" y="0.5" width="6" height="11" rx="1.2" fill="none" stroke="#fff" stroke-width="1.2"/></svg>209 555-0187</li>
    <li><svg viewBox="0 0 12 12"><rect x="0.5" y="2" width="11" height="8" fill="#fff"/><path d="M0.5 2 L6 6.5 L11.5 2" fill="none" stroke="var(--brand-blue)" stroke-width="1"/></svg>hello@clearlineplumbing.com</li>
    <li><svg viewBox="0 0 12 12"><path d="M2 10 L10 2" stroke="#fff" stroke-width="1.6"/><circle cx="3" cy="9" r="2" fill="none" stroke="#fff"/><circle cx="9" cy="3" r="2" fill="none" stroke="#fff"/></svg>www.clearlineplumbing.com</li>
  </ul>
</section>

</body>
</html>
```